Kestrel Facilities Business Card Design

We would now like to design business cards with the new Kestrel Facilities logo

Target Market(s)

Professional

Industry/Entity Type

Professional services

Contact Information for Business Card

Employee name, title, phone number, email address, corporate office address and logo.

Font styles to use
Sans Serif

Colors
0054AA
0677BA
7BADD7
CADEEF
E8F1F8

Requirements
Must have
• My logo
Should not have
• any other pictures or images besides my logo

```html
<!DOCTYPE html>
<html lang="en">
<head>
<meta charset="utf-8">
<title>Kestrel Facilities Business Card</title>
<link href="https://fonts.googleapis.com/css2?family=Montserrat:wght@400;500;700&display=swap" rel="stylesheet">
<style>
  :root {
    --brand-blue: #3174bc;
    --brand-deep: #0054aa;
    --swoosh-grey: #a7a8aa;
    --card-white: #ffffff;
    --ink: #1b1b1b;
    --logo-silver: #dfe3ea;
    --page-bg: #e8f1f8;
  }
  html, body {
    margin: 0;
    width: 1200px;
    height: 960px;
    overflow: hidden;
    background: var(--page-bg);
    font-family: "Montserrat", sans-serif;
  }
  .sheet {
    width: 1200px;
    height: 960px;
    display: flex;
    flex-direction: column;
    align-items: center;
    justify-content: center;
    gap: 44px;
  }
  .card {
    position: relative;
    width: 720px;
    height: 411px;
    border-radius: 22px;
    overflow: hidden;
    box-shadow: 0 8px 22px rgba(0, 40, 90, 0.18);
  }
  .card-back {
    background: var(--brand-blue);
    display: flex;
    align-items: center;
    justify-content: center;
  }
  .wordmark {
    display: flex;
    align-items: center;
    gap: 16px;
    font-weight: 700;
    letter-spacing: 0.04em;
    text-transform: uppercase;
    white-space: nowrap;
  }
  .wordmark-mark {
    width: 38px;
    height: 38px;
    border-radius: 50%;
    flex: none;
  }
  .card-back .wordmark { color: var(--logo-silver); font-size: 40px; }
  .card-back .wordmark-mark { background: var(--logo-silver); }
  .card-front { background: var(--card-white); }
  .front-waves { position: absolute; inset: 0; width: 100%; height: 100%; }
  .holder {
    position: absolute;
    left: 44px;
    top: 128px;
    color: var(--card-white);
  }
  .holder-name {
    margin: 0;
    font-weight: 700;
    font-size: 26px;
    letter-spacing: 0.02em;
  }
  .holder-title {
    margin: 4px 0 0 18px;
    font-weight: 400;
    font-size: 19px;
  }
  .card-front .wordmark {
    position: absolute;
    right: 40px;
    top: 246px;
    color: var(--brand-blue);
    font-size: 28px;
    gap: 12px;
  }
  .card-front .wordmark-mark { width: 28px; height: 28px; background: var(--brand-blue); }
  .contact {
    position: absolute;
    left: 150px;
    top: 282px;
    color: var(--ink);
    font-size: 15px;
    line-height: 1.35;
  }
  .contact-address { margin: 0 0 10px; }
  .contact-list { list-style: none; margin: 0; padding: 0; }
  .contact-list li { display: flex; align-items: center; gap: 8px; }
  .contact-icon { width: 14px; height: 14px; fill: var(--brand-blue); flex: none; }
</style>
</head>
<body>
<main class="sheet">
  <section class="card card-back" aria-label="Card back">
    <div class="wordmark"><span class="wordmark-mark"></span>Kestrel Facilities</div>
  </section>

  <section class="card card-front" aria-label="Card front">
    <svg class="front-waves" viewBox="0 0 720 411" preserveAspectRatio="none" aria-hidden="true">
      <path d="M0 0 H720 V40 C610 30 560 70 500 130 C420 210 300 225 0 245 Z" fill="var(--brand-blue)"/>
      <path d="M720 40 C610 30 560 70 500 130 C420 210 300 225 0 245 V257 C300 237 425 222 508 140 C570 80 615 48 720 54 Z" fill="var(--swoosh-grey)"/>
      <path d="M720 66 C630 64 585 100 540 150 C595 108 640 86 720 80 Z" fill="var(--brand-blue)"/>
      <path d="M0 262 C180 250 300 240 380 222 C300 248 180 262 0 270 Z" fill="var(--brand-blue)"/>
    </svg>

    <div class="holder">
      <h1 class="holder-name">DANA WHITCOMBE</h1>
      <p class="holder-title">Co-Founder</p>
    </div>

    <div class="wordmark"><span class="wordmark-mark"></span>Kestrel Facilities</div>

    <div class="contact">
      <p class="contact-address">418 Harbor View Road<br>Suite 210 Fairhaven.12</p>
      <ul class="contact-list">
        <li><svg class="contact-icon" viewBox="0 0 24 24"><path d="M6.6 10.8a15.1 15.1 0 0 0 6.6 6.6l2.2-2.2a1 1 0 0 1 1-.25 11.4 11.4 0 0 0 3.6.57 1 1 0 0 1 1 1V20a1 1 0 0 1-1 1A17 17 0 0 1 3 4a1 1 0 0 1 1-1h3.5a1 1 0 0 1 1 1c0 1.25.2 2.45.57 3.6a1 1 0 0 1-.25 1z"/></svg>+254-700-41275</li>
        <li><svg class="contact-icon" viewBox="0 0 24 24"><path d="M2 5h20v14H2z M2 5l10 8 10-8" fill="none" stroke="var(--brand-blue)" stroke-width="2.4"/></svg>info@kestrelfacilities.com</li>
        <li><svg class="contact-icon" viewBox="0 0 24 24"><circle cx="12" cy="12" r="10"/><path d="M2 12h20M12 2c3 3 3 17 0 20M12 2c-3 3-3 17 0 20" fill="none" stroke="#fff" stroke-width="1.5"/></svg>www.kestrelfacilities.com</li>
      </ul>
    </div>
  </section>
</main>
</body>
</html>
```